Business Card Design for company

We want new business cards. We'd like something different-- yet still highly professional. Our tagline is Providing leadership, delivering success. Stock photos are ok, as long as they are relevant and look upscale.

Target Market(s)

Architecture/Business Management Consulting/Engineering Consulting

Contact Information for Business Card

dark gray background with pops of blue might be good, but you tell me. You're the designers. Rounded corners might be nice, but again, you tell me.

Font styles to use
Serif
Sans Serif

Colors
3276b5
5c5c5c
9d9d9d
fbfbfb

Requirements
Nice to have
• Something different, but still very professional.

```html
<!DOCTYPE html>
<html lang="en">
<head>
<meta charset="utf-8">
<title>Norvale Group — Business Cards</title>
<link rel="stylesheet" href="https://fonts.googleapis.com/css2?family=Montserrat:wght@500;600;700&family=Work+Sans:wght@400;500&display=swap">
<style>
  :root {
    --brand-blue: #2a6499;
    --accent-blue: #3276b5;
    --ink-gray: #4a4d55;
    --text-gray: #5c5c5c;
    --soft-gray: #9d9d9d;
    --paper: #fbfbfb;
    --backdrop: #a9a9a9;
  }
  html, body {
    margin: 0;
    padding: 0;
    width: 1200px;
    height: 930px;
    overflow: hidden;
    background: var(--backdrop);
  }
  .canvas {
    position: relative;
    width: 1200px;
    height: 930px;
    background: radial-gradient(ellipse at 45% 40%, #c4c4c4 0%, var(--backdrop) 70%);
  }
  .card {
    position: absolute;
    width: 560px;
    height: 320px;
    border-radius: 22px;
    box-shadow: 0 6px 14px rgba(0,0,0,0.25);
    overflow: hidden;
  }

  /* Back side */
  .card--back {
    left: 90px;
    top: 110px;
    background: var(--brand-blue);
    color: var(--paper);
  }
  .card--back .company-name {
    position: absolute;
    left: 0;
    right: 0;
    top: 108px;
    text-align: center;
    font-family: "Montserrat", sans-serif;
    font-weight: 700;
    font-size: 40px;
    letter-spacing: 3px;
    color: var(--paper);
  }
  .card--back .web-rule {
    position: absolute;
    left: 40px;
    right: 40px;
    bottom: 50px;
    display: flex;
    align-items: center;
    gap: 14px;
    font-family: "Work Sans", sans-serif;
    font-size: 14px;
    letter-spacing: 0.5px;
    color: var(--paper);
  }
  .card--back .web-rule::before,
  .card--back .web-rule::after {
    content: "";
    flex: 1;
    height: 1px;
    background: rgba(251,251,251,0.75);
  }

  /* Front side */
  .card--front {
    left: 550px;
    top: 500px;
    background: var(--paper);
  }
  .brand {
    position: absolute;
    left: 40px;
    top: 122px;
    width: 230px;
    display: flex;
    align-items: flex-start;
    gap: 12px;
  }
  .brand-square {
    flex: none;
    width: 18px;
    height: 18px;
    margin-top: 9px;
    background: var(--brand-blue);
  }
  .brand-name {
    font-family: "Montserrat", sans-serif;
    font-weight: 700;
    font-size: 32px;
    line-height: 1.1;
    letter-spacing: 1.5px;
    color: var(--brand-blue);
  }
  .divider {
    position: absolute;
    left: 292px;
    top: 70px;
    width: 1px;
    height: 170px;
    background: linear-gradient(to bottom, var(--accent-blue), rgba(50,118,181,0.2));
  }
  .details {
    position: absolute;
    left: 316px;
    top: 66px;
    font-family: "Work Sans", sans-serif;
    color: var(--text-gray);
    font-size: 13px;
    line-height: 1.45;
  }
  .person-name {
    font-family: "Montserrat", sans-serif;
    font-weight: 600;
    font-size: 20px;
    letter-spacing: 0.8px;
    color: var(--accent-blue);
    margin: 0;
  }
  .person-role {
    margin: 0 0 10px 0;
    font-size: 13px;
  }
  .address {
    margin: 0 0 8px 0;
    font-style: normal;
  }
  .contact-list {
    list-style: none;
    margin: 0;
    padding: 0;
  }
  .contact-list li {
    display: flex;
    align-items: center;
    gap: 8px;
  }
  .contact-list svg {
    width: 11px;
    height: 11px;
    flex: none;
  }
  .contact-list .web strong {
    color: var(--accent-blue);
    font-weight: 500;
  }
</style>
</head>
<body>
<main class="canvas">

  <section class="card card--back" aria-label="Card back">
    <div class="company-name">NORVALE GROUP</div>
    <div class="web-rule">www.norvalegroup.com</div>
  </section>

  <section class="card card--front" aria-label="Card front">
    <div class="brand">
      <span class="brand-square"></span>
      <span class="brand-name">NORVALE<br>GROUP</span>
    </div>

    <div class="divider"></div>

    <div class="details">
      <h1 class="person-name">DANIEL HART</h1>
      <p class="person-role">Director</p>
      <address class="address">27 Harbour Lane,<br>Westbridge, 4021</address>
      <ul class="contact-list">
        <li>
          <svg viewBox="0 0 12 12" aria-hidden="true"><path d="M3 1 L5 3.5 L4 5 C4.8 6.6 5.6 7.4 7 8 L8.5 7 L11 9 L9.8 11 C5.5 10.6 1.4 6.5 1 2.2 Z" fill="#3276b5"/></svg>
          (555) 014-2270
        </li>
        <li>
          <svg viewBox="0 0 12 12" aria-hidden="true"><rect x="1" y="2.5" width="10" height="7" rx="1" fill="none" stroke="#3276b5" stroke-width="1.3"/><path d="M1.5 3 L6 6.5 L10.5 3" fill="none" stroke="#3276b5" stroke-width="1.2"/></svg>
          info@norvalegroup.com
        </li>
        <li class="web">
          <svg viewBox="0 0 12 12" aria-hidden="true"><circle cx="6" cy="6" r="5" fill="none" stroke="#3276b5" stroke-width="1.2"/><ellipse cx="6" cy="6" rx="2.2" ry="5" fill="none" stroke="#3276b5" stroke-width="1"/><path d="M1 6 H11" stroke="#3276b5" stroke-width="1"/></svg>
          <span>www.<strong>norvalegroup</strong>.com</span>
        </li>
      </ul>
    </div>
  </section>

</main>
</body>
</html>
```